Poster for a Bicycle show/Expo

We need a poster for a Bicycle show/Expo and sustainable transport. Exhibitors will sell bikes, cycling clothing, accessories, etc. ...
This show is annual and the Poster is for the 2015 edition.

The style must be modern, dynamic, bright colors.

Your concept must be compatible in a landscape format. (We will ourselves adaptations of different formats.)
Width: 210 mm
Height: 297 mm
It's necessary for us to have the source file (vector) for make, later, the different format (flyers, website, ...)

Content of the Poster:
- 1 big picture (no clip art)
- Big title: « Foire du Rayon » (« Salon » or « Salon du » can be small and « Vélo » big.)
- Subtitle: « et de la mobilité douce »
- Date: « 8, 9 et 10 mai 2015 » or « 8-10 mai 2015 »
- Place: « Halle TRV - Gare de Lunel »
- Text line 1: « www.foire-du-rayon.ch - Entrée gratuite »
- Text line 2« Piste d’essais - Restauration sur place »
- Text line 3: « Ve 8 mai de 17h à 21h - Sa 9 mai de 10h à 20h - Di 10 mai de 10h à 18h »
- Please, leave a zone in the poster for sponsors logos
(The predominant information (most visible) are: « Foire du Rayon » and « 8, 9 et 10 mai 2015 or 8-10 mai 2015 »)

Content of the big picture:
- from a cheap stock, like PixKiosk.com
- a bicycle in action or a detail of a bicycle (or a accessory) (no race bike)
- a modern picture with bright colors.
- if a person is on the picture, we prefer a men
- not an aerial view with cyclists in a landscape.

Some examples of poster of shows - with typo-title worked

http://www.expobassinlutece.com/Temp/IMG/F_a9b3c2d4e5f60718293a4b5c6d7e8f9012345678901_200_296.png

http://qx4m.tornafoire.fr/Data/pvtorn_mer/block/F_7cc1bb9396aef1d5e69283647561f0076457c357c5ea6.pdf
(page 2 of this PDF)

http://salons.rivol-evenements.fr/images/rivol-evenements/foires-salons/phototheque/salon-auto-bourlac/salon-auto-bourlac2012-affiche.jpg

http://www.tirovel.net/blog/wp-content/uploads/2007/03/affiche-salon-du-livre.jpg

http://www.quaimarin-gens.com/wp-content/affiche-cannes-2007.jpg
Updates

Hello,

For information, for your next versions, please, add the text "Piste d'essais".

- Text line 1: « www.foire-du-rayon.ch - Entrée gratuite »
- Text line 2: « Piste d’essais - Restauration sur place »
- Text line 3: « Ve 8 mai de 17h à 21h - Sa 9 mai de 10h à 20h - Di 10 mai de 10h à 18h »

Thanks,
Rodolphe

```html
<!DOCTYPE html>
<html lang="fr">
<head>
<meta charset="utf-8">
<title>Foire du Rayon et de la mobilité douce 2015</title>
<link href="https://fonts.googleapis.com/css2?family=Marcellus&family=Montserrat:wght@400;500&display=swap" rel="stylesheet">
<style>
  :root {
    --plum: #a54f8b;
    --orange: #f08a30;
    --sky: rgba(34, 176, 236, 0.93);
    --white: #ffffff;
    --photo-light: #e9edf0;
    --photo-mid: #c9d2d8;
    --photo-blue: #3fa6d8;
  }
  * { margin: 0; padding: 0; box-sizing: border-box; }
  html, body { width: 1200px; height: 849px; overflow: hidden; }
  body { font-family: "Montserrat", Arial, sans-serif; color: var(--white); }

  .poster { position: relative; width: 1200px; height: 849px; overflow: hidden; }

  .hero-photo {
    position: absolute; inset: 0;
    background:
      radial-gradient(ellipse 160px 120px at 240px 180px, var(--photo-blue), transparent 70%),
      radial-gradient(ellipse 120px 200px at 1120px 150px, rgba(63,166,216,0.7), transparent 70%),
      radial-gradient(ellipse 500px 300px at 200px 500px, #f6f7f8, transparent 70%),
      linear-gradient(160deg, var(--photo-mid) 0%, var(--photo-light) 45%, #d7dde2 75%, #b9c6cf 100%);
  }

  .band { position: absolute; left: 351px; width: 548px; }

  .subtitle {
    top: 90px; height: 43px; background: var(--plum);
    font-size: 29px; font-weight: 400; line-height: 43px; padding-left: 20px;
  }

  .event-info { top: 141px; height: 83px; background: var(--plum); padding: 8px 0 0 20px; }
  .event-date { font-size: 22px; line-height: 32px; }
  .event-date .day { font-size: 30px; }
  .event-date .joiner { font-size: 19px; }
  .event-venue { font-size: 19px; line-height: 30px; margin-top: 2px; }

  .practical {
    position: absolute; top: 231px; height: 81px; background: var(--orange);
    font-size: 18.5px; line-height: 22px; padding: 7px 0 0 19px;
  }
  .practical--access { left: 351px; width: 271px; }
  .practical--hours { left: 628px; width: 271px; padding-left: 20px; }

  .title-block {
    position: absolute; left: 351px; top: 320px; width: 548px; height: 438px;
    background: var(--sky);
  }
  .event-title {
    position: absolute; left: 68px; top: 52px;
    font-family: "Marcellus", Georgia, serif; font-weight: 400;
    font-size: 108px; line-height: 98px; letter-spacing: 2px;
    color: var(--white); text-transform: uppercase;
  }
  .event-title span { display: block; }

  .sponsor-zone {
    position: absolute; left: 899px; top: 320px; width: 210px; height: 438px;
    background: var(--white);
  }
</style>
</head>
<body>
  <main class="poster">
    <div class="hero-photo" role="img" aria-label="Photo en gros plan d'une sonnette de vélo bleue avec boussole sur un guidon blanc"></div>

    <div class="band subtitle">et de la mobilité douce</div>

    <div class="band event-info">
      <p class="event-date"><span class="day">8</span>, <span class="day">9</span> <span class="joiner">et</span> <span class="day">10</span> MAI 2015</p>
      <p class="event-venue">» Halle TRV - Gare de Lunel</p>
    </div>

    <div class="practical practical--access">
      <p>www.foire-du-rayon.ch</p>
      <p>Entrée gratuite</p>
      <p>Restauration sur place</p>
    </div>

    <div class="practical practical--hours">
      <p>Ve 8 mai de 17h à 21h</p>
      <p>Sa 9 mai de 10h à 20h</p>
      <p>Di 10 mai de 10h à 18h</p>
    </div>

    <section class="title-block">
      <h1 class="event-title"><span>Foire</span><span>du</span><span>Rayon</span></h1>
    </section>

    <aside class="sponsor-zone" aria-label="Zone réservée aux logos des partenaires"></aside>
  </main>
</body>
</html>
```